Book cover design for a collection of poetry - The Lanternfield

Book cover and back design need to be moody, nostalgic, reflective, ethereal. Melancholy and other worldly. Cover design should not be time specific to a period or place but if applicable should reflect British landscape. Book cover should be in tones of blue and must include the title and author (THE LANTERNFIELD BY CORBIN WHITLACE). We love the idea of rain, and looking out of a window. See attached designs. A world you are observing but not in.

Industry/Entity Type

Book Publisher

Font styles to use
Serif
Script

Colors
3176b5
3377b5
85acd3
eaf1f7
0792cd
33a6d7
86cae7
ecf7fb
86cfc6

Requirements
Must have
• The colour blue in it, must be melancholy and reflective.
Nice to have
• Rain in the cover.
Should not have
• Any bright colours.

```html
<!DOCTYPE html>
<html lang="en">
<head>
<meta charset="utf-8">
<title>The Lanternfield — Cover Spread</title>
<link rel="stylesheet" href="https://fonts.googleapis.com/css2?family=Bodoni+Moda:opsz,wght@6..96,500;6..96,700&family=Playfair+Display:wght@700&family=Archivo:wght@400&display=swap">
<style>
  :root {
    --paper: #ffffff;
    --sky-deep: #1f63d8;
    --sky-mid: #3aa6ec;
    --sky-light: #6cc6f4;
    --orchid: #a779e8;
    --orchid-deep: #8a5fd6;
    --water-dark: #2a5fc9;
    --title-shadow: #2f7be0;
    --back-blue: #52cdf5;
    --panel: #f6f9fa;
    --blurb: #1ab4ea;
    --frame: #ffffff;
  }
  * { margin: 0; padding: 0; box-sizing: border-box; }
  html, body { width: 1200px; height: 820px; overflow: hidden; background: var(--paper); }
  .spread { position: relative; width: 1200px; height: 820px; }

  /* Front cover */
  .front-cover {
    position: absolute; left: 0; top: 0; width: 586px; height: 820px; overflow: hidden;
    border: 1px solid #1a2a40;
  }
  .front-artwork {
    position: absolute; inset: 0;
    background:
      radial-gradient(ellipse 34% 16% at 14% 8%, rgba(170,120,235,.95), rgba(167,121,232,.5) 55%, transparent 80%),
      radial-gradient(ellipse 26% 10% at 48% 10%, rgba(160,110,225,.85), transparent 75%),
      radial-gradient(ellipse 12% 8% at 8% 22%, rgba(150,100,230,.8), transparent 80%),
      radial-gradient(circle at 82% 22%, rgba(120,210,255,.55), transparent 14%),
      radial-gradient(circle at 92% 8%, rgba(60,190,170,.5), transparent 12%),
      radial-gradient(ellipse 28% 5% at 49% 68%, rgba(40,60,210,.85), rgba(90,110,230,.45) 55%, transparent 85%),
      radial-gradient(ellipse 70% 12% at 50% 66%, rgba(150,160,240,.35), transparent 80%),
      radial-gradient(ellipse 90% 10% at 50% 57%, rgba(200,210,255,.25), transparent 80%),
      radial-gradient(circle at 30% 93%, rgba(170,230,255,.45), transparent 4%),
      radial-gradient(circle at 62% 96%, rgba(170,230,255,.45), transparent 4%),
      radial-gradient(circle at 85% 90%, rgba(170,230,255,.4), transparent 3%),
      linear-gradient(180deg, #2a8be6 0%, var(--sky-mid) 18%, var(--sky-light) 36%, #5eaaf0 50%, #5a9cec 62%, #3a72d8 74%, var(--water-dark) 84%, #3a78dc 100%);
  }
  .cover-title {
    position: absolute; left: 0; right: 0; top: 142px; text-align: center;
    font-family: "Bodoni Moda", "Playfair Display", serif; font-weight: 700;
    color: var(--paper); line-height: 1;
    text-shadow: 4px 3px 0 var(--title-shadow);
  }
  .cover-title .title-lead { display: block; font-size: 98px; letter-spacing: 1px; }
  .cover-title .title-main { display: block; font-size: 62px; letter-spacing: 0; margin-top: 44px; }
  .author-band {
    position: absolute; left: 0; right: 0; top: 655px; height: 62px;
    border-top: 2px solid var(--paper); border-bottom: 2px solid var(--paper);
    display: flex; align-items: center; justify-content: center;
  }
  .author-name {
    font-family: "Playfair Display", serif; font-weight: 700; font-size: 35px;
    color: var(--paper); letter-spacing: .5px; transform: scaleX(.8);
  }

  /* Back cover */
  .back-cover {
    position: absolute; left: 614px; top: 0; width: 586px; height: 820px;
    background: var(--back-blue);
  }
  .back-frame {
    position: absolute; left: 40px; top: 54px; width: 505px; height: 712px;
    border: 3px solid var(--frame);
  }
  .back-panel {
    position: absolute; left: 43px; top: 188px; width: 499px; height: 429px;
    background: var(--panel);
  }
  .ornament { position: absolute; left: 55px; width: 475px; }
  .ornament-top {
    top: 62px; height: 175px;
    background: radial-gradient(ellipse 50% 55% at 50% 80%, #ffffff 0%, rgba(255,255,255,.85) 55%, rgba(255,255,255,0) 100%);
  }
  .ornament-bottom {
    top: 560px; height: 178px;
    background: radial-gradient(ellipse 50% 55% at 50% 20%, #ffffff 0%, rgba(255,255,255,.85) 55%, rgba(255,255,255,0) 100%);
  }
  .blurb {
    position: absolute; left: 107px; top: 268px; width: 370px; text-align: center;
    font-family: "Archivo", Arial, sans-serif; font-size: 11px; line-height: 16.7px;
    letter-spacing: 2.1px; text-transform: uppercase; color: var(--blurb);
  }
  .blurb p + p { margin-top: 16.7px; }
</style>
</head>
<body>
<main class="spread">
  <section class="front-cover">
    <div class="front-artwork" role="img" aria-label="Purple orchid blossoms above still blue water, raindrops falling into a rippling pool with sparkling droplets below"></div>
    <h1 class="cover-title">
      <span class="title-lead">THE</span>
      <span class="title-main">LANTERNFIELD</span>
    </h1>
    <div class="author-band">
      <p class="author-name">CORBIN WHITLACE</p>
    </div>
  </section>

  <section class="back-cover">
    <div class="back-panel"></div>
    <div class="ornament ornament-top" role="img" aria-label="White filigree scroll ornament"></div>
    <div class="ornament ornament-bottom" role="img" aria-label="White filigree scroll ornament"></div>
    <div class="back-frame"></div>
    <div class="blurb">
      <p>The Lanternfield is a collection of poetry.</p>
      <p>Told in two parts we first meet Charles – aged, crippled and left alone in his inherited marsh house - reflecting on his life and his marriage to beautiful Alice who we meet in part two. Alice is suicidal, manically depressed and struggling with life as a wife and mother. She meets, harbors and falls in love with a soldier during WWII and her world is changed forever.</p>
      <p>Moving through the 20th century, this life and the next, The Lanternfield interweaves grief, loss, the after-life, mental illness, and ultimately the true nature of love.</p>
    </div>
  </section>
</main>
</body>
</html>
```